LHP Regal Business Card Design 2020

Your Manor Steward is looking for a business card that is clean and straight to the point but still looks high-end and attractive. We are a team comprised of management and field professionals focused on the high-end residential marketplace. We serve homeowners and trade professionals directly based out of the Metrowest/Boston area. We provide client services as well as construction/renovation services.
We are aiming for a black and white feel (white background and black text) and a matte finish with rounded edges.

We want to emphasis our vision of "Properties - Projects - Partners".
Dana Pellham is the president of LHP

Please include the following areas we service: Boston/Cape/Newport
Please make sure to include Dana's mobile (555) 213 4480 & office number (555) 640 1937, email dana@yourmanorsteward.example and website www.yourmanorsteward.example

Colors

Designer to choose only greyscale colors for use in the design.

Requirements
Must have
• Include "Properties - Projects - Partners" in design

Include "After Hours Emergency Support # 1800 555 0142" with icon

```html
<!DOCTYPE html>
<html lang="en">
<head>
<meta charset="utf-8">
<title>LHP Business Card</title>
<link rel="stylesheet" href="https://fonts.googleapis.com/css2?family=Montserrat:wght@500;700;800&display=swap">
<style>
  :root {
    --stage: #e6e6e6;
    --ink: #1f1f1f;
    --card-dark: #232323;
    --card-light: #ffffff;
    --paper-text: #ffffff;
    --muted: #3a3a3a;
    --rule: #cfcfcf;
  }
  * { margin: 0; padding: 0; box-sizing: border-box; }
  html, body { width: 1200px; height: 800px; overflow: hidden; }
  body {
    background: var(--stage);
    font-family: "Montserrat", Arial, sans-serif;
    display: flex;
    align-items: center;
    justify-content: center;
    gap: 60px;
  }
  .card {
    width: 525px;
    height: 300px;
    border-radius: 12px;
    position: relative;
    box-shadow: 0 6px 18px rgba(0,0,0,0.12);
    overflow: hidden;
  }
  .card-front {
    background: var(--card-dark);
    color: var(--paper-text);
    display: flex;
    flex-direction: column;
    align-items: center;
    padding-top: 62px;
  }
  .brand-mark {
    font-weight: 800;
    font-size: 86px;
    line-height: 1;
    letter-spacing: -2px;
  }
  .brand-name {
    margin-top: 12px;
    font-weight: 800;
    font-size: 15px;
    letter-spacing: 3px;
    text-transform: uppercase;
  }
  .tagline {
    margin-top: 10px;
    font-size: 11px;
    font-weight: 500;
    letter-spacing: 2px;
    text-transform: uppercase;
    opacity: 0.85;
  }
  .service-areas {
    position: absolute;
    bottom: 24px;
    left: 0; right: 0;
    text-align: center;
    font-size: 11px;
    font-weight: 500;
    letter-spacing: 0.3px;
  }
  .service-areas span::before {
    content: "\25CF";
    font-size: 7px;
    margin: 0 4px 0 8px;
    vertical-align: 2px;
  }
  .card-back {
    background: var(--card-light);
    color: var(--ink);
    padding: 34px 40px;
  }
  .card-back .brand-mark { font-size: 54px; }
  .card-back .brand-name { font-size: 10px; margin-top: 6px; letter-spacing: 2px; }
  .holder-name {
    margin-top: 28px;
    font-weight: 800;
    font-size: 16px;
    text-transform: uppercase;
  }
  .holder-title { font-size: 12px; font-weight: 700; margin-top: 2px; }
  .contact-grid {
    margin-top: 10px;
    display: grid;
    grid-template-columns: auto auto;
    column-gap: 18px;
    row-gap: 4px;
    justify-content: start;
    font-size: 11.5px;
    font-weight: 500;
    color: var(--muted);
  }
  .contact-item { display: flex; align-items: center; gap: 5px; white-space: nowrap; }
  .contact-item svg, .emergency svg { width: 11px; height: 11px; fill: var(--ink); flex: none; }
  .emergency {
    margin-top: 12px;
    padding-top: 9px;
    border-top: 1px solid var(--rule);
    display: flex;
    align-items: center;
    gap: 6px;
    font-size: 11px;
    font-weight: 700;
    color: var(--ink);
    white-space: nowrap;
  }
</style>
</head>
<body>
  <section class="card card-front" aria-label="Card front">
    <div class="brand-mark">LHP</div>
    <div class="brand-name">Your Manor Steward</div>
    <div class="tagline">Properties - Projects - Partners</div>
    <div class="service-areas"><span>Boston</span><span>Metrowest</span><span>South Shore</span><span>Cape</span><span>Newport</span></div>
  </section>

  <section class="card card-back" aria-label="Card back">
    <div class="brand-mark">LHP</div>
    <div class="brand-name">Your Manor Steward</div>
    <div class="holder-name">Dana Pellham</div>
    <div class="holder-title">President</div>
    <div class="contact-grid">
      <div class="contact-item">
        <svg viewBox="0 0 12 12" aria-hidden="true"><path d="M3 0h6a1 1 0 0 1 1 1v10a1 1 0 0 1-1 1H3a1 1 0 0 1-1-1V1a1 1 0 0 1 1-1zm0 1.5v8h6v-8zM6 10.2a.6.6 0 1 0 0 1.2.6.6 0 0 0 0-1.2z"/></svg>
        (555) 213 4480
      </div>
      <div class="contact-item">
        <svg viewBox="0 0 12 12" aria-hidden="true"><path d="M0 2h12v8H0zM1 3v.4l5 3.2 5-3.2V3zm0 1.6V9h10V4.6L6 7.8z"/></svg>
        dana@yourmanorsteward.example
      </div>
      <div class="contact-item">
        <svg viewBox="0 0 12 12" aria-hidden="true"><path d="M1 4c0-1.5 2-2.5 5-2.5S11 2.5 11 4v1H8.5V4h-5v1H1zm1.5 2h7l1.5 5H1z"/></svg>
        (555) 640 1937
      </div>
      <div class="contact-item">
        <svg viewBox="0 0 12 12" aria-hidden="true"><path d="M6 0a6 6 0 1 0 0 12A6 6 0 0 0 6 0zm0 1c.6 0 1.4 1.3 1.7 3.5H4.3C4.6 2.3 5.4 1 6 1zM1.1 5.5h2.1a12 12 0 0 0 0 1H1.1zm0 1.5h2.2c.2 1.5.6 2.8 1.2 3.6A5 5 0 0 1 1.1 7zm3.2 0h3.4C7.4 9.5 6.6 11 6 11S4.6 9.5 4.3 7zm4.4 0h2.2a5 5 0 0 1-3.4 3.6C8.1 9.8 8.5 8.5 8.7 7zm0-1.5h2.2v1H8.8zm-4.4 0h3.4v1H4.3zM7.5 1.4A5 5 0 0 1 10.9 4.5H8.7c-.2-1.5-.6-2.4-1.2-3.1zm-3 0c-.6.7-1 1.6-1.2 3.1H1.1a5 5 0 0 1 3.4-3.1z"/></svg>
        www.yourmanorsteward.example
      </div>
    </div>
    <div class="emergency">
      <svg viewBox="0 0 12 12" aria-hidden="true"><path d="M2.4.5l2 2.2-1.1 1.4c.7 1.6 2 2.9 3.6 3.6l1.4-1.1 2.2 2-1.3 2C5 10.6 1.4 7 .4 1.8z"/></svg>
      After Hours Emergency Support # 1800 555 0142
    </div>
  </section>
</body>
</html>
```